Ductless Mini Split Business Website

Copper Fern Services is looking to design an eye catching educational website about installing Ductless mini splits.

Similar to this company.
https://www.halvikstream.com/

Coding

Coded - Design and coding required

```html
<!DOCTYPE html>
<html lang="en">
<head>
<meta charset="utf-8">
<title>Copper Fern Services – Ductless Experts</title>
<link href="https://fonts.googleapis.com/css2?family=Mulish:wght@400;600;700;800&family=Raleway:wght@300;400;500;600;700&display=swap" rel="stylesheet">
<style>
:root{
  --yellow:#ffd400;
  --black:#121212;
  --ink:#1b1b1b;
  --panel:#4a4a4a;
  --panel-dark:#3b3b3b;
  --white:#ffffff;
  --muted:#d8d8d8;
  --line:#3a3a3a;
}
*{box-sizing:border-box;margin:0;padding:0}
html,body{width:1200px;height:4858px;overflow:hidden}
body{background:var(--black);font-family:"Mulish",sans-serif;color:var(--white);position:relative}
.abs{position:absolute}
.brand-name{font-family:"Mulish",sans-serif;font-weight:800;color:var(--yellow);line-height:1}
.btn{position:absolute;display:flex;align-items:center;justify-content:center;gap:10px;border-radius:30px;font-weight:700;font-size:17px;font-family:"Mulish",sans-serif}
.btn-solid{background:var(--yellow);color:var(--black)}
.btn-outline{border:2px solid var(--yellow);color:var(--yellow)}
.arrow{width:16px;height:16px;border-radius:50%;background:currentColor;position:relative}
.btn-solid .arrow{background:var(--black)}
.arrow::after{content:"";position:absolute;left:5px;top:5px;border-left:7px solid var(--yellow);border-top:3px solid transparent;border-bottom:3px solid transparent}
.btn-outline .arrow::after{border-left-color:var(--black)}
.mascot{position:absolute;width:34px;height:26px;border-radius:10px;background:linear-gradient(135deg,#ffd400,#8a7a2a)}
.section-title{position:absolute;left:0;width:1200px;text-align:center;font-family:"Raleway",sans-serif;font-weight:400;font-size:38px;color:var(--white)}
.section-title b{color:var(--yellow);font-weight:700}
.lead{position:absolute;left:130px;width:940px;text-align:center;font-size:17px;line-height:36px;color:var(--white)}
.divider{position:absolute;left:89px;width:1021px;height:1px;background:var(--line)}

/* header */
.header{position:absolute;left:0;top:0;width:1200px;height:130px;background:var(--black)}
.search{position:absolute;left:452px;top:20px;width:250px;height:40px;border:1px solid #bbb;border-radius:20px;font-size:14px;color:#aaa;padding:10px 16px}
.search i{position:absolute;right:4px;top:4px;width:30px;height:30px;border-radius:50%;background:var(--yellow)}
.contact-chip{position:absolute;top:18px;display:flex;gap:12px;align-items:center;font-size:15px;line-height:22px}
.contact-chip b{font-weight:700}
.nav{position:absolute;top:102px;left:367px;display:flex;gap:30px;font-size:15px}
.nav .on{color:var(--yellow);font-weight:700}
.dot-social{position:absolute;top:105px;width:14px;height:14px;border-radius:50%;border:2px solid var(--white)}

/* hero */
.hero{position:absolute;left:0;top:130px;width:1200px;height:720px}
.hero-photo{position:absolute;inset:0;background:linear-gradient(100deg,#e9ecec 0%,#c8cdcd 45%,#a2a8aa 75%,#8a8f90 100%)}
.hero h1{position:absolute;left:89px;top:178px;font-family:"Raleway",sans-serif;font-weight:500;font-size:46px;color:#222}
.hero p{position:absolute;left:91px;top:240px;width:515px;font-size:20px;line-height:40px;color:#333;letter-spacing:.3px}

/* services */
.card{position:absolute;width:331px;height:333px}
.card .photo{position:absolute;left:0;top:0;width:331px;height:225px}
.card .body{position:absolute;left:17px;top:190px;width:297px;height:143px;background:var(--panel);border-top:3px solid var(--yellow);text-align:center}
.card h3{font-size:17px;font-weight:700;color:var(--yellow);margin-top:22px}
.card p{font-size:12px;line-height:25px;color:var(--muted);margin-top:8px;padding:0 12px}
.pager{position:absolute;top:2312px;width:16px;height:16px;border-radius:50%;border:2px solid var(--yellow)}
.pager.on{background:radial-gradient(circle,var(--yellow) 35%,transparent 40%)}

/* why */
.why{position:absolute;left:0;top:2411px;width:1200px;height:693px}
.feature-icon{position:absolute;left:562px;width:82px;height:82px;border-radius:50%;background:var(--yellow);border:4px solid var(--white);display:flex;align-items:center;justify-content:center}
.feature h4{position:absolute;left:676px;font-size:22px;font-weight:700;color:var(--white)}
.feature p{position:absolute;left:676px;width:434px;font-size:14px;line-height:31px;color:var(--muted);text-align:justify}

/* about */
.about-art{position:absolute;left:110px;top:3180px;width:440px;height:340px;border-radius:8px;background:linear-gradient(135deg,#2b2b2b 0%,#5a4c12 45%,#8f7813 60%,#2b2b2b 100%)}

/* contact form */
.field{position:absolute;height:38px;border:2px solid #cfcfcf;font-size:12px;color:#ddd;padding:9px 12px}
.field::before{content:"";display:inline-block;width:8px;height:8px;background:#ddd;margin-right:6px}

/* footer */
.footer-col h5{font-size:16px;font-weight:700;color:var(--yellow);margin-bottom:14px}
.footer-col a{display:block;font-size:15px;color:var(--white);line-height:36px;text-decoration:none}
.follow{position:absolute;width:28px;height:28px;border-radius:50%;border:2px solid var(--white);top:4492px}
</style>
</head>
<body>

<!-- Header -->
<header class="header">
  <div class="abs" style="left:95px;top:22px;width:36px;height:36px;border-radius:50%;background:var(--yellow)"></div>
  <div class="brand-name abs" style="left:140px;top:24px;font-size:26px">Copper Fern<br><span style="font-size:18px">Services</span></div>
  <div class="brand-name abs" style="left:98px;top:100px;font-size:20px;letter-spacing:1px">DUCTLESS EXPERTS</div>
  <div class="search">Search<i></i></div>
  <div class="contact-chip" style="left:728px">
    <svg width="30" height="30" viewBox="0 0 24 24"><rect width="24" height="24" rx="5" fill="#ffd400"/><path d="M7 5l3 3-2 2c1 2 3 4 5 5l2-2 3 3-2 3C10 19 5 14 5 7z" fill="#121212"/></svg>
    <div>Call us<br><b>555 014 2290</b></div>
  </div>
  <div class="contact-chip" style="left:908px">
    <svg width="38" height="28" viewBox="0 0 38 28"><rect x="1" y="2" width="36" height="24" rx="3" fill="#ffd400"/><path d="M2 4l17 12 17-12" stroke="#121212" stroke-width="3" fill="none"/></svg>
    <div>Email us<br><b>hello@copperfern.co</b></div>
  </div>
  <nav class="nav">
    <span class="on">Home</span><span>About Us</span><span>Our Services</span><span>Ductless Heat Pumps</span><span>Reviews</span><span>Contact Us</span>
  </nav>
  <span class="dot-social" style="left:1068px"></span>
  <span class="dot-social" style="left:1096px"></span>
</header>

<!-- Hero -->
<section class="hero">
  <div class="hero-photo" role="img" aria-label="Photo of a woman relaxing on a sofa under a wall-mounted ductless air conditioner"></div>
  <div class="mascot" style="left:91px;top:148px" role="img" aria-label="Small bee mascot"></div>
  <h1>Copper Fern Services</h1>
  <p>Lorem ipsum dolor sit amet, consectetur adipiscing elit, sed do eiusmod tempor incididunt ut labore et dolore magna aliqua.</p>
  <div class="btn btn-solid" style="left:90px;top:365px;width:206px;height:52px">Get a Quote <span class="arrow"></span></div>
  <svg class="abs" style="left:0;top:0" width="1200" height="720">
    <polygon points="0,645 1200,720 0,720" fill="#121212"/>
    <polygon points="760,695 1200,607 1200,715" fill="#ffd400"/>
  </svg>
</section>

<!-- Welcome -->
<div class="mascot" style="left:583px;top:928px" role="img" aria-label="Small bee mascot"></div>
<h2 class="section-title" style="top:965px">Welcome to <b>Copper Fern Services</b></h2>
<p class="lead" style="top:1025px;text-align:justify;text-align-last:center">Our mission is to give cost-effective and effective power alternatives and items which are self-sustainable. One of the key inclusions of our mission viewpoint is the participation of the group in creating power alternatives for self and becoming a role model for others.</p>
<div class="btn btn-outline" style="left:388px;top:1155px;width:206px;height:52px">Read More <span class="arrow"></span></div>
<div class="btn btn-solid" style="left:607px;top:1155px;width:206px;height:52px">Get a Quote <span class="arrow"></span></div>
<div class="divider" style="top:1287px"></div>

<!-- Services -->
<div class="mascot" style="left:583px;top:1372px" role="img" aria-label="Small bee mascot"></div>
<h2 class="section-title" style="top:1410px">Our <b>Services</b></h2>
<p class="lead" style="top:1472px;left:120px;width:960px">Sed ut perspiciatis unde omnis iste natus error sit voluptatem accusantium doloremque laudantium, totam rem aperiam, eaque ipsa quae ab illo inventore veritatis et quasi architecto beatae vitae dicta sunt explicabo.</p>

<div class="card" style="left:77px;top:1574px"><div class="photo" role="img" aria-label="Technician repairing an outdoor heat pump unit" style="background:linear-gradient(135deg,#9aa3a8,#5b6064)"></div><div class="body"><h3>Baseboard Heat Replacement</h3><p>Sed ut perspiciatis unde omnis iste natus error sit voluptatem accusantium doloremque laudantium eaque veritatis</p></div></div>
<div class="card" style="left:435px;top:1574px"><div class="photo" role="img" aria-label="Gloves and pressure gauges on a service unit" style="background:linear-gradient(135deg,#8f8a7c,#c6a23c 60%,#5b5b5b)"></div><div class="body"><h3>Ductless Maintenance</h3><p>Sed ut perspiciatis unde omnis iste natus error sit voluptatem accusantium doloremque laudantium eaque veritatis</p></div></div>
<div class="card" style="left:793px;top:1574px"><div class="photo" role="img" aria-label="Technician inspecting an indoor wall unit" style="background:linear-gradient(135deg,#e3e6e8,#9ea6ab)"></div><div class="body"><h3>Ductless Repair</h3><p>Sed ut perspiciatis unde omnis iste natus error sit voluptatem accusantium doloremque laudantium eaque veritatis</p></div></div>
<div class="card" style="left:77px;top:1945px"><div class="photo" role="img" aria-label="Technician checking refrigerant gauges at outdoor units" style="background:linear-gradient(135deg,#cfd6da,#7d8a92)"></div><div class="body"><h3>Ductless Heat Pump FAQ</h3><p>Sed ut perspiciatis unde omnis iste natus error sit voluptatem accusantium doloremque laudantium eaque veritatis</p></div></div>
<div class="card" style="left:435px;top:1945px"><div class="photo" role="img" aria-label="Installer mounting a ceiling unit" style="background:linear-gradient(135deg,#eceeee,#b9bdbe)"></div><div class="body"><h3>Ductless Installation</h3><p>Sed ut perspiciatis unde omnis iste natus error sit voluptatem accusantium doloremque laudantium eaque veritatis</p></div></div>
<div class="card" style="left:793px;top:1945px"><div class="photo" role="img" aria-label="Woman using a remote for a wall unit" style="background:linear-gradient(135deg,#e6eaec,#8ea6bb)"></div><div class="body"><h3>Ductless Warranty</h3><p>Sed ut perspiciatis unde omnis iste natus error sit voluptatem accusantium doloremque laudantium eaque veritatis</p></div></div>
<span class="pager on" style="left:566px"></span><span class="pager" style="left:591px"></span><span class="pager" style="left:616px"></span>

<!-- Why choose us -->
<section class="why">
  <div class="abs" style="left:0;top:0;width:600px;height:693px;background:linear-gradient(120deg,#8d8a84,#5e5b56 60%,#46443f)" role="img" aria-label="Photo of a couple sitting in a cozy living room"></div>
  <div class="abs" style="left:600px;top:0;width:600px;height:693px;background:var(--panel-dark)"></div>
  <svg class="abs" style="left:0;top:0" width="1200" height="693">
    <polygon points="0,0 600,0 600,20 0,110" fill="#ffd400"/>
    <polygon points="560,665 1200,575 1200,693 600,693" fill="#ffd400"/>
    <polygon points="0,663 560,665 600,693 0,693" fill="#121212"/>
  </svg>
  <div class="mascot" style="left:91px;top:195px" role="img" aria-label="Small bee mascot"></div>
  <h2 class="abs" style="left:89px;top:228px;font-family:'Raleway',sans-serif;font-weight:300;font-size:36px">Why Choose <b style="color:var(--yellow);font-weight:700">Us</b></h2>
  <p class="abs" style="left:89px;top:290px;width:405px;font-size:16px;line-height:36px;text-align:justify">Lorem ipsum dolor sit amet, consectetur adipiscing elit, sed do eiusmod tempor incididunt ut labore et dolore magna aliqua. Quis ipsum suspendisse ultrices gravida.</p>
  <div class="btn btn-solid" style="left:89px;top:450px;width:206px;height:52px">Read More <span class="arrow"></span></div>

  <div class="feature">
    <div class="feature-icon" style="top:89px"><svg width="36" height="36" viewBox="0 0 24 24"><rect x="5" y="3" width="14" height="18" rx="2" fill="none" stroke="#121212" stroke-width="2"/><path d="M8 16v-3M12 16v-6M16 16v-8" stroke="#121212" stroke-width="2"/></svg></div>
    <h4 style="top:102px">0% Financing for 60 months</h4>
    <p style="top:139px">Sed ut perspiciatis unde omnis iste natus error sit voluptatem accusantium doloremque laudantium, totam rem aperiam, evitae dicta sunt explicabo.</p>
  </div>
  <div class="feature">
    <div class="feature-icon" style="top:266px"><svg width="36" height="36" viewBox="0 0 24 24"><circle cx="12" cy="9" r="6" fill="none" stroke="#121212" stroke-width="2"/><path d="M3 19c3-2 6-2 9 0s6 0 9-2" stroke="#121212" stroke-width="2" fill="none"/></svg></div>
    <h4 style="top:279px">365 Day, Money Back Guarantee</h4>
    <p style="top:316px">Sed ut perspiciatis unde omnis iste natus error sit voluptatem accusantium doloremque laudantium, totam rem aperiam, evitae dicta sunt explicabo.</p>
  </div>
  <div class="feature">
    <div class="feature-icon" style="top:444px"><svg width="36" height="36" viewBox="0 0 24 24"><path d="M4 4l16 16M20 4L4 20" stroke="#121212" stroke-width="2.5"/></svg></div>
    <h4 style="top:457px">We Are Experts In Ductless Services</h4>
    <p style="top:494px">Sed ut perspiciatis unde omnis iste natus error sit voluptatem accusantium doloremque laudantium, totam rem aperiam, evitae dicta sunt explicabo.</p>
  </div>
</section>

<!-- About -->
<div class="about-art" role="img" aria-label="Illustration of the bee mascot holding a wrench and a screwdriver"></div>
<div class="mascot" style="left:600px;top:3188px" role="img" aria-label="Small bee mascot"></div>
<h2 class="abs" style="left:600px;top:3230px;font-family:'Raleway',sans-serif;font-weight:400;font-size:38px">About <b style="color:var(--yellow);font-weight:700">Us</b></h2>
<p class="abs" style="left:600px;top:3283px;width:505px;font-size:16px;line-height:36px;text-align:justify">Sed ut perspiciatis unde omnis iste natus error sit voluptatem accusantium doloremque laudantium, totam rem aperiam, eaque ipsa quae ab illo inventore veritatis et quasi architecto beatae vitae dicta sunt explicabo. Nemo enim ipsam voluptatem quia voluptas sit aspernatur aut odit aut fugit nesciunt.</p>
<div class="btn btn-solid" style="left:600px;top:3494px;width:208px;height:54px">Read More <span class="arrow"></span></div>
<div class="divider" style="top:3608px"></div>

<!-- Contact -->
<div class="mascot" style="left:583px;top:3692px" role="img" aria-label="Small bee mascot"></div>
<h2 class="section-title" style="top:3730px">Contact <b>Copper Fern Services</b></h2>
<p class="lead" style="top:3790px;left:100px;width:1000px">At vero eos et accusamus et iusto odio dignissimos ducimus qui blanditiis praesentium voluptatum deleniti atque corrupti quos dolores et quas molestias excepturi sint occaecati cupiditate non provident</p>
<div class="field" style="left:89px;top:3887px;width:502px">First Name</div>
<div class="field" style="left:611px;top:3887px;width:499px">Last Name</div>
<div class="field" style="left:89px;top:3942px;width:502px">Company</div>
<div class="field" style="left:89px;top:3996px;width:502px">Email Address</div>
<div class="field" style="left:89px;top:4050px;width:502px">Phone Number</div>
<div class="field" style="left:611px;top:3942px;width:499px;height:146px">Message :</div>
<div class="btn btn-solid" style="left:496px;top:4117px;width:208px;height:54px">Submit
  <svg width="18" height="16" viewBox="0 0 18 16"><path d="M1 7L17 1 13 15 9 10z" fill="#121212"/></svg></div>

<!-- Footer -->
<footer>
  <div class="abs" style="left:0;top:4290px;width:1200px;height:568px;background:linear-gradient(180deg,#202020,#171717 60%,#2a2624)" role="img" aria-label="Dim photo of a living room with a wall-mounted air conditioner"></div>
  <svg class="abs" style="left:0;top:4246px" width="1200" height="120"><polygon points="0,0 800,44 0,108" fill="#ffd400"/><polygon points="0,0 1200,0 1200,44 800,44" fill="#121212"/></svg>
  <div class="abs" style="left:95px;top:4455px;width:40px;height:40px;border-radius:50%;background:var(--yellow)"></div>
  <div class="brand-name abs" style="left:145px;top:4456px;font-size:30px">Copper Fern<br><span style="font-size:20px">Services</span></div>
  <div class="brand-name abs" style="left:100px;top:4520px;font-size:26px;letter-spacing:1px">DUCTLESS EXPERTS</div>
  <div class="abs" style="left:830px;top:4498px;font-size:15px;font-weight:700">FOLLOW US :</div>
  <span class="follow" style="left:938px"></span><span class="follow" style="left:973px"></span><span class="follow" style="left:1008px"></span><span class="follow" style="left:1043px"></span><span class="follow" style="left:1078px"></span>
  <div class="abs" style="left:89px;top:4560px;width:1021px;height:1px;background:#444"></div>

  <div class="footer-col abs" style="left:91px;top:4590px"><h5>NAVIGATION</h5><a>Home</a><a>About Us</a><a>Our Services</a><a>Ductless Heat Pumps</a><a>Reviews</a></div>
  <div class="footer-col abs" style="left:329px;top:4590px"><h5>LINKS</h5><a>Terms &amp; Conditions</a><a>Privacy Policy</a><a>Site Map</a><a>Disclaimer</a><a>Contact Us</a></div>
  <div class="footer-col abs" style="left:537px;top:4590px;width:260px">
    <h5>CONTACT INFO</h5>
    <div style="display:flex;gap:10px;font-size:13px;line-height:26px"><svg width="14" height="20" viewBox="0 0 14 20"><path d="M7 0a7 7 0 0 1 7 7c0 5-7 13-7 13S0 12 0 7a7 7 0 0 1 7-7z" fill="#fff"/><circle cx="7" cy="7" r="2.5" fill="#121212"/></svg><span>4180 Alder Crest Lane, Marlow<br>Texas - 77490</span></div>
    <div style="display:flex;gap:10px;font-size:13px;margin-top:14px"><svg width="14" height="14" viewBox="0 0 24 24"><path d="M6 2l4 4-2 3c1 3 4 6 7 7l3-2 4 4-3 4C10 22 2 14 2 5z" fill="#fff"/></svg>Help : +1 555 014 2290</div>
    <div style="display:flex;gap:10px;font-size:13px;margin-top:20px"><svg width="16" height="12" viewBox="0 0 16 12"><rect width="16" height="12" fill="#fff"/><path d="M0 0l8 6 8-6" stroke="#121212" fill="none"/></svg>hello@copperfern.co</div>
  </div>
  <div class="footer-col abs" style="left:835px;top:4590px"><h5>NEWSLETTER</h5></div>
  <div class="abs" style="left:835px;top:4635px;width:275px;height:40px;background:var(--white);font-size:12px;color:#999;padding:12px 14px">Enter e-mail address</div>
  <div class="btn btn-solid" style="left:835px;top:4690px;width:155px;height:40px;font-size:15px">Subscribe</div>
  <div class="abs" style="left:0;top:4827px;width:1200px;text-align:center;font-size:12px">Copyrights© Copper Fern Services. 2019 | Allrights Reserved.</div>
</footer>

</body>
</html>
```